Non fiction leadership Book Cover design needed for “Stay Bold: Build On Lasting Discipline”

I need a front cover design for a new book 6 X 9 traditional non-fiction book.

Title: "Stay BOLD - Build On Lasting Discipline"

The subtitle is not finalized- so use 2 lines of smaller dummy text

My brand guide is attached (please use the tan color sparingly)

I'd like to see BOLD look like it is in motion and "flying" across the page

Need CREATIVE designs and options

Do not want my picture on the front cover - I do want it on the back cover.

On the front cover I’d like to see creative use of font to create movement on “BOLD”

Target Market(s)

Business leaders

Industry/Entity Type

Aviation

Font styles to use
Other font styles liked:
• See style guide- can add additional font (modern script or san serif)

Colors
0054AA
0677BA
7BADD7
CADEEF
E8F1F8
EB3D1F
EC4F4E
F09395
F8D3D4
FCEDEE

Requirements
Must have
• Creative font use, using perspective to create movement/motion on BOLD
Should not have
• My picture on the front cover- my picture should be on the back cover

```html
<!DOCTYPE html>
<html lang="en">
<head>
<meta charset="utf-8">
<title>Stay Bold: Build On Lasting Discipline — Front Cover</title>
<link rel="stylesheet" href="https://fonts.googleapis.com/css2?family=Bebas+Neue&family=Montserrat:wght@500;600&display=swap">
<style>
  :root {
    --backdrop: #adacaa;
    --navy: #0a1a5c;
    --cream: #f9f2ec;
    --white: #ffffff;
    --emblem: #efe6dd;
    --brand-blue: #0054aa;
    --brand-sky: #0677ba;
    --brand-mist: #7badd7;
    --brand-pale: #cadeef;
    --brand-red: #eb3d1f;
    --tan: #c99c66;
  }
  * { margin: 0; padding: 0; box-sizing: border-box; }
  html, body {
    width: 1200px; height: 960px; overflow: hidden;
    background: var(--backdrop);
  }
  .cover {
    position: absolute; left: 300px; top: 30px;
    width: 600px; height: 900px;
    background: var(--cream);
    overflow: hidden;
    box-shadow: 0 6px 18px rgba(0,0,0,0.18);
  }
  .top-band {
    position: absolute; left: 0; top: 0;
    width: 600px; height: 219px;
    background: var(--navy);
  }
  .teaser {
    position: absolute; left: 0; top: 32px; width: 600px;
    text-align: center;
    font-family: "Montserrat", sans-serif; font-weight: 500;
    font-size: 12.5px; line-height: 17px;
    color: var(--white);
  }
  .emblem {
    position: absolute; left: 245px; top: 82px;
    width: 110px; height: 137px;
    background: var(--emblem);
    border-radius: 6px;
  }
  .title-svg {
    position: absolute; left: 0; top: 230px;
    width: 600px; height: 510px;
  }
  .title-small { font-family: "Bebas Neue", sans-serif; fill: var(--navy); }
  .title-large { font-family: "Bebas Neue", sans-serif; }
  .letter-shadow { fill: var(--navy); }
  .letter-face { fill: url(#blue-rise); }
  .speed-line { stroke-linecap: round; }
  .subtitle-bar {
    position: absolute; left: 71px; top: 756px;
    width: 458px; height: 48px;
    background: var(--navy);
    display: flex; align-items: center; justify-content: center;
  }
  .subtitle {
    font-family: "Montserrat", sans-serif; font-weight: 600;
    font-size: 19px; letter-spacing: 0.5px;
    color: var(--white); white-space: nowrap;
  }
  .author {
    position: absolute; left: 0; top: 822px; width: 600px;
    text-align: center;
    font-family: "Montserrat", sans-serif; font-weight: 600;
    font-size: 34px; color: var(--navy);
  }
</style>
</head>
<body>
  <main class="cover">
    <header class="top-band">
      <p class="teaser">Lorem ipsum dolor sit amet, consectetuer adipiscing<br>sed diam nonummy nibh euismod tincidunt</p>
      <div class="emblem" role="img" aria-label="White silhouette of a helicopter seen from above, rotor blades crossed"></div>
    </header>

    <svg class="title-svg" viewBox="0 0 600 510" aria-label="Stay BOLD">
      <defs>
        <linearGradient id="blue-rise" x1="0" y1="0" x2="0" y2="1">
          <stop offset="0" stop-color="var(--brand-mist)"/>
          <stop offset="0.45" stop-color="var(--brand-sky)"/>
          <stop offset="1" stop-color="var(--brand-blue)"/>
        </linearGradient>
      </defs>

      <text class="title-small" x="210" y="108" font-size="134" textLength="188" lengthAdjust="spacingAndGlyphs">STAY</text>

      <g class="speed-lines">
        <line class="speed-line" x1="8" y1="300" x2="62" y2="300" stroke="var(--brand-pale)" stroke-width="6"/>
        <line class="speed-line" x1="22" y1="340" x2="70" y2="340" stroke="var(--brand-mist)" stroke-width="8"/>
        <line class="speed-line" x1="4" y1="382" x2="66" y2="382" stroke="var(--brand-sky)" stroke-width="5"/>
        <line class="speed-line" x1="30" y1="420" x2="64" y2="420" stroke="var(--brand-red)" stroke-width="4"/>
        <line class="speed-line" x1="14" y1="458" x2="58" y2="458" stroke="var(--tan)" stroke-width="3"/>
      </g>

      <g class="bold-word" transform="translate(0,500) skewX(-10) translate(0,-500)">
        <text class="title-large letter-shadow" x="64" y="496" font-size="400" textLength="96" lengthAdjust="spacingAndGlyphs">B</text>
        <text class="title-large letter-face" x="70" y="500" font-size="400" textLength="96" lengthAdjust="spacingAndGlyphs">B</text>

        <text class="title-large letter-shadow" x="172" y="496" font-size="445" textLength="106" lengthAdjust="spacingAndGlyphs">O</text>
        <text class="title-large letter-face" x="178" y="500" font-size="445" textLength="106" lengthAdjust="spacingAndGlyphs">O</text>

        <text class="title-large letter-shadow" x="290" y="496" font-size="490" textLength="98" lengthAdjust="spacingAndGlyphs">L</text>
        <text class="title-large letter-face" x="296" y="500" font-size="490" textLength="98" lengthAdjust="spacingAndGlyphs">L</text>

        <text class="title-large letter-shadow" x="392" y="496" font-size="535" textLength="118" lengthAdjust="spacingAndGlyphs">D</text>
        <text class="title-large letter-face" x="398" y="500" font-size="535" textLength="118" lengthAdjust="spacingAndGlyphs">D</text>
      </g>
    </svg>

    <div class="subtitle-bar"><span class="subtitle">BUILD ON LASTING DISCIPLINE</span></div>
    <p class="author">Margaret Holloway</p>
  </main>
</body>
</html>
```